Rollers & Glides.com

Vertical Business Card with focus on branding with our icon. Information on card will be logo, persons name, position, phone number, email address and website. Use the the name Marcus Pellow, position President, phone number 480.915.2267, email Marcus@rollersandglides-demo.com, website www.rollersandglides-demo.com.

```html
<!DOCTYPE html>
<html lang="en">
<head>
<meta charset="utf-8">
<title>Rollers &amp; Glides.com — Business Card</title>
<link rel="stylesheet" href="https://fonts.googleapis.com/css2?family=Montserrat:wght@400;700&family=Roboto:wght@500&display=swap">
<style>
  :root {
    --backdrop: #ececec;
    --paper: #f7f7f5;
    --brand-blue: #1d45a8;
    --brand-blue-deep: #1a3f9e;
    --brand-blue-mid: #5570c4;
    --brand-silver: #b4c0e4;
    --ink-grey: #3b3b3b;
    --white: #ffffff;
  }
  * { margin: 0; padding: 0; box-sizing: border-box; }
  html, body {
    width: 1200px;
    height: 986px;
    overflow: hidden;
    background: var(--backdrop);
  }
  .canvas {
    position: relative;
    width: 1200px;
    height: 986px;
  }
  .card {
    position: absolute;
    top: 181px;
    width: 366px;
    height: 657px;
    overflow: hidden;
  }
  .card-front {
    left: 168px;
    background: var(--paper);
    text-align: center;
    font-family: "Montserrat", sans-serif;
  }
  .card-back {
    left: 697px;
    background: var(--brand-blue);
  }
  .brand-name {
    position: absolute;
    left: 0;
    right: 0;
    top: 138px;
    font-weight: 700;
    font-size: 27px;
    line-height: 34px;
    color: var(--brand-blue);
  }
  .person-name {
    position: absolute;
    left: 0; right: 0;
    top: 333px;
    font-weight: 700;
    font-size: 22px;
    letter-spacing: 0.5px;
    color: var(--brand-blue);
  }
  .person-role {
    position: absolute;
    left: 0; right: 0;
    top: 364px;
    font-family: "Roboto", sans-serif;
    font-weight: 500;
    font-size: 20px;
    color: var(--ink-grey);
  }
  .contact-icons {
    position: absolute;
    left: 0; right: 0;
    top: 428px;
    display: flex;
    justify-content: center;
    gap: 6px;
  }
  .contact-lines {
    position: absolute;
    left: 0; right: 0;
    top: 463px;
    font-size: 17px;
    line-height: 25px;
    color: var(--ink-grey);
  }
  .divider {
    position: absolute;
    left: 166px;
    top: 532px;
    width: 34px;
    height: 3px;
    background: var(--brand-blue);
  }
  .website {
    position: absolute;
    left: 0; right: 0;
    top: 545px;
    font-size: 17px;
    color: var(--ink-grey);
  }
  .pattern-field {
    position: absolute;
    inset: 0;
    background: linear-gradient(160deg,
      var(--brand-silver) 0%,
      var(--brand-blue-mid) 28%,
      var(--brand-blue) 62%,
      var(--brand-blue-deep) 100%);
  }
  .back-brand {
    position: absolute;
    right: 36px;
    top: 546px;
    font-family: "Montserrat", sans-serif;
    font-weight: 700;
    font-size: 16px;
    color: var(--white);
  }
</style>
</head>
<body>
<main class="canvas">
  <section class="card card-front" aria-label="Business card front">
    <p class="brand-name">Rollers &amp; Glides.com</p>
    <h1 class="person-name">MARCUS PELLOW</h1>
    <p class="person-role">President</p>
    <div class="contact-icons">
      <svg width="22" height="22" viewBox="0 0 22 22" aria-label="Phone">
        <circle cx="11" cy="11" r="11" fill="var(--brand-blue)"/>
        <path d="M7.5 6.2c.4-.4 1-.4 1.3 0l1.1 1.4c.3.4.3.9-.1 1.2l-.6.6c.6 1.3 1.6 2.3 2.9 2.9l.6-.6c.3-.4.9-.4 1.2-.1l1.4 1.1c.4.3.4.9 0 1.3l-.8.8c-.6.6-1.6.7-2.4.3-2.2-1.1-3.9-2.8-5-5-.4-.8-.3-1.8.3-2.4z" fill="var(--white)"/>
      </svg>
      <svg width="22" height="22" viewBox="0 0 22 22" aria-label="Email">
        <circle cx="11" cy="11" r="11" fill="var(--brand-blue)"/>
        <rect x="6" y="7.5" width="10" height="7" rx="1" fill="none" stroke="var(--white)" stroke-width="1.4"/>
        <path d="M6.5 8l4.5 3.5L15.5 8" fill="none" stroke="var(--white)" stroke-width="1.4"/>
      </svg>
    </div>
    <p class="contact-lines">480.915.2267<br>Marcus@rollersandglides-demo.com</p>
    <div class="divider"></div>
    <p class="website">www.rollersandglides-demo.com</p>
  </section>

  <section class="card card-back" aria-label="Business card back">
    <div class="pattern-field" role="img" aria-label="Repeating embossed brand pattern fading from silver to deep blue"></div>
    <p class="back-brand">Rollers &amp; Glides.com</p>
  </section>
</main>
</body>
</html>
```